Brainwave state designs for neurofeedback report

Design ORIGINAL graphics that correspond with existing colors and shapes for Halo Prism Grid of Stillness & Halo Prism Rhythm Panel for "Normal", "Bright Harbor", "Summit Tide" etc... patterns. You can change the shape of the white outline to be more modern looking. Perhaps you can also use white background with black outline. The frequency bars (can be more ordered) but keep the general shape of the outline.

• An original flair. Modern. Neurotechish
• Do not copy the design. Add your original ideas. Choose a font that complements the design.

```html
<!DOCTYPE html>
<html lang="en">
<head>
<meta charset="utf-8">
<title>The Halo Prism Grid of Stillness</title>
<link rel="stylesheet" href="https://fonts.googleapis.com/css2?family=Poppins:ital,wght@0,800;1,700&family=Barlow+Condensed:wght@600&family=Roboto:ital,wght@0,300;1,300&display=swap">
<style>
  :root {
    --ink: #111111;
    --label-ink: #333333;
    --axis-ink: #666666;
    --grid: #e2e2e2;
    --marker: #d8232a;
    --scale-bar: #e3172d;
    --beta: #f0612e;
    --alpha: #14803c;
    --theta: #5b8fd0;
    --delta: #9b2f9b;
    --band-beta: #fff3ec;
    --band-alpha: #eef7f0;
    --band-theta: #eef3fb;
    --band-delta: #f7eef7;
    --f38: #e84a35;
    --f30: #ea5433;
    --f24: #ef6b37;
    --f19: #f38d3a;
    --f15: #f6a43a;
    --f125: #5e9e50;
    --f105: #2e8b3d;
    --f9: #1e6e34;
    --f75: #5a9ad4;
    --f6: #6b84c8;
    --f4: #7c6bb8;
    --f3: #8a58b0;
    --f15d: #9a42a0;
    --f075: #9a3a9a;
    --berg-top: #3a4048;
    --berg-mid: #8a97a5;
    --berg-deep: #11151a;
  }
  html, body {
    margin: 0;
    padding: 0;
    width: 1200px;
    height: 675px;
    overflow: hidden;
    background: #ffffff;
  }
  .canvas {
    position: relative;
    width: 1200px;
    height: 675px;
  }
  .title {
    position: absolute;
    left: 0;
    width: 1208px;
    top: 56px;
    margin: 0;
    text-align: center;
    font-family: "Poppins", sans-serif;
    font-weight: 800;
    font-size: 30px;
    letter-spacing: 0.3px;
    color: var(--ink);
  }
  .chart {
    position: absolute;
    left: 0;
    top: 0;
  }
  .freq-label {
    font-family: "Barlow Condensed", sans-serif;
    font-weight: 600;
    font-size: 17px;
    fill: var(--label-ink);
  }
  .axis-label {
    font-family: "Roboto", sans-serif;
    font-weight: 300;
    font-size: 13px;
    fill: var(--axis-ink);
  }
  .axis-title {
    font-family: "Roboto", sans-serif;
    font-style: italic;
    font-weight: 300;
    font-size: 16px;
    fill: #555555;
  }
  .state-label {
    font-family: "Poppins", sans-serif;
    font-style: italic;
    font-weight: 700;
    font-size: 16.5px;
  }
  .state-beta { fill: var(--beta); }
  .state-alpha { fill: var(--alpha); }
  .state-theta { fill: var(--theta); }
  .state-delta { fill: var(--delta); }
  .iceberg-panel {
    position: absolute;
    left: 752px;
    top: 149px;
    width: 352px;
    height: 445px;
    background: linear-gradient(180deg, var(--berg-top) 0%, #4a525c 30%, var(--berg-mid) 34%, #c9d2da 38%, #5a6674 44%, #2c3440 70%, var(--berg-deep) 100%);
  }
</style>
</head>
<body>
<main class="canvas">
  <h1 class="title">THE HALO PRISM GRID OF STILLNESS</h1>

  <div class="iceberg-panel" role="img" aria-label="Iceberg with a small peak above the waterline and a large mass below it"></div>

  <svg class="chart" width="1200" height="675" viewBox="0 0 1200 675" aria-label="Brainwave amplitude by frequency, left and right hemispheres">
    <g class="state-bands">
      <rect x="120" y="161" width="430" height="125.4" rx="8" fill="var(--band-beta)"/>
      <rect x="120" y="286.4" width="430" height="75.9" fill="var(--band-alpha)"/>
      <rect x="120" y="362.3" width="430" height="75.5" fill="var(--band-theta)"/>
      <rect x="120" y="437.8" width="430" height="80.2" rx="8" fill="var(--band-delta)"/>
    </g>

    <g class="grid-lines" stroke="var(--grid)" stroke-width="0.8">
      <line x1="134" y1="161" x2="134" y2="518"/>
      <line x1="170" y1="161" x2="170" y2="518"/>
      <line x1="206" y1="161" x2="206" y2="518"/>
      <line x1="243" y1="161" x2="243" y2="518"/>
      <line x1="279" y1="161" x2="279" y2="518"/>
      <line x1="389" y1="161" x2="389" y2="518"/>
      <line x1="425" y1="161" x2="425" y2="518"/>
      <line x1="461" y1="161" x2="461" y2="518"/>
      <line x1="497" y1="161" x2="497" y2="518"/>
      <line x1="534" y1="161" x2="534" y2="518"/>
    </g>

    <g class="bars-left">
      <rect x="275.6" y="169.3" width="28.2" height="10" rx="5" fill="var(--f38)"/>
      <rect x="280.3" y="194.6" width="23.5" height="10" rx="5" fill="var(--f30)"/>
      <rect x="263.9" y="219.9" width="39.9" height="10" rx="5" fill="var(--f24)"/>
      <rect x="248.9" y="244.7" width="54.9" height="10" rx="5" fill="var(--f19)"/>
      <rect x="244.2" y="270.1" width="59.6" height="10" rx="5" fill="var(--f15)"/>
      <rect x="243.8" y="294.9" width="60.0" height="10" rx="5" fill="var(--f125)"/>
      <rect x="196.9" y="320.2" width="106.9" height="10" rx="5" fill="var(--f105)"/>
      <rect x="213.3" y="345.1" width="90.5" height="10" rx="5" fill="var(--f9)"/>
      <rect x="259.7" y="369.9" width="44.1" height="10" rx="5" fill="var(--f75)"/>
      <rect x="246.6" y="395.2" width="57.2" height="10" rx="5" fill="var(--f6)"/>
      <rect x="264.4" y="420.1" width="39.4" height="10" rx="5" fill="var(--f4)"/>
      <rect x="227.3" y="445.4" width="76.5" height="10" rx="5" fill="var(--f3)"/>
      <rect x="239.1" y="470.7" width="64.7" height="10" rx="5" fill="var(--f15d)"/>
      <rect x="283.1" y="496.0" width="20.7" height="10" rx="5" fill="var(--f075)"/>
    </g>

    <g class="bars-right">
      <rect x="366.6" y="169.3" width="37.5" height="10" rx="5" fill="var(--f38)"/>
      <rect x="366.6" y="194.6" width="27.2" height="10" rx="5" fill="var(--f30)"/>
      <rect x="366.6" y="219.9" width="37.5" height="10" rx="5" fill="var(--f24)"/>
      <rect x="366.6" y="244.7" width="41.2" height="10" rx="5" fill="var(--f19)"/>
      <rect x="366.6" y="270.1" width="51.5" height="10" rx="5" fill="var(--f15)"/>
      <rect x="366.6" y="294.9" width="63.7" height="10" rx="5" fill="var(--f125)"/>
      <rect x="366.6" y="320.2" width="125.1" height="10" rx="5" fill="var(--f105)"/>
      <rect x="366.6" y="345.1" width="125.1" height="10" rx="5" fill="var(--f9)"/>
      <rect x="366.6" y="369.9" width="37.5" height="10" rx="5" fill="var(--f75)"/>
      <rect x="366.6" y="395.2" width="66.5" height="10" rx="5" fill="var(--f6)"/>
      <rect x="366.6" y="420.1" width="46.8" height="10" rx="5" fill="var(--f4)"/>
      <rect x="366.6" y="445.4" width="66.5" height="10" rx="5" fill="var(--f3)"/>
      <rect x="366.6" y="470.7" width="53.4" height="10" rx="5" fill="var(--f15d)"/>
      <rect x="366.6" y="496.0" width="18.2" height="10" rx="5" fill="var(--f075)"/>
    </g>

    <g class="freq-labels" text-anchor="middle">
      <text class="freq-label" x="335.6" y="180.5">38</text>
      <text class="freq-label" x="335.6" y="205.8">30</text>
      <text class="freq-label" x="335.6" y="231.1">24</text>
      <text class="freq-label" x="335.6" y="255.9">19</text>
      <text class="freq-label" x="335.6" y="281.3">15</text>
      <text class="freq-label" x="335.6" y="306.1">12.5</text>
      <text class="freq-label" x="335.6" y="331.4">10.5</text>
      <text class="freq-label" x="335.6" y="356.3">9</text>
      <text class="freq-label" x="335.6" y="381.1">7.5</text>
      <text class="freq-label" x="335.6" y="406.4">6</text>
      <text class="freq-label" x="335.6" y="431.3">4</text>
      <text class="freq-label" x="335.6" y="456.6">3</text>
      <text class="freq-label" x="335.6" y="481.9">1.5</text>
      <text class="freq-label" x="335.6" y="507.2">0.75</text>
    </g>

    <g class="outline" fill="none" stroke="var(--ink)" stroke-width="2.2" stroke-linecap="round" stroke-linejoin="round">
      <path d="M270.9,165 Q265.3,174.8 268.35,187.25 Q271.4,199.7 263.45,213.05 Q255.5,226.4 247.3,237.4 Q239.1,248.4 236.75,260.15 Q234.4,271.9 233.7,285.45 Q233,299 205.5,311.2 Q178,323.4 185.5,336.3 Q193,349.2 220.7,361.65 Q248.4,374.1 240,386.95 Q231.6,399.8 242.15,412.5 Q252.7,425.2 234.15,438.05 Q215.6,450.9 221.7,463.35 Q227.8,475.8 250.05,488.2 L272.3,500.6"/>
      <path d="M407.8,165.5 Q416.3,175.8 410.4,187.75 Q404.5,199.7 408.95,212.35 Q413.4,225 414.85,237.4 Q416.3,249.8 422.35,262.5 Q428.4,275.2 435,287.1 Q441.6,299 474.8,311.7 Q508,324.4 508,337.05 Q508,349.7 461.9,362.35 Q415.8,375 431.25,387.65 Q446.7,400.3 435.7,412.75 Q424.7,425.2 436.4,438.3 Q448.1,451.4 441.3,463.6 Q434.5,475.8 418.1,488.2 L401.7,500.6"/>
    </g>

    <g class="state-dividers" stroke="var(--marker)" stroke-width="1.2" stroke-dasharray="12 7">
      <line x1="87" y1="286.4" x2="884" y2="286.4"/>
      <line x1="87" y1="362.3" x2="884" y2="362.3"/>
      <line x1="87" y1="437.8" x2="884" y2="437.8"/>
    </g>

    <g class="axis" text-anchor="middle">
      <text class="axis-label" x="134" y="538">15</text>
      <text class="axis-label" x="170" y="538">12</text>
      <text class="axis-label" x="206" y="538">9</text>
      <text class="axis-label" x="243" y="538">6</text>
      <text class="axis-label" x="279" y="538">3</text>
      <text class="axis-label" x="389" y="538">3</text>
      <text class="axis-label" x="425" y="538">6</text>
      <text class="axis-label" x="461" y="538">9</text>
      <text class="axis-label" x="497" y="538">12</text>
      <text class="axis-label" x="535" y="538">15</text>
      <rect x="143" y="550.3" width="160.3" height="6.5" rx="3.25" fill="var(--scale-bar)"/>
      <rect x="366.6" y="550.3" width="160.3" height="6.5" rx="3.25" fill="var(--scale-bar)"/>
      <text class="axis-title" x="334.7" y="560">sEMG</text>
    </g>

    <g class="state-labels" text-anchor="middle">
      <text class="state-label state-beta" x="634" y="221.5">BETA</text>
      <text class="state-label state-beta" x="634" y="241.5">CONSCIOUS MIND</text>
      <text class="state-label state-alpha" x="634" y="319.5">ALPHA</text>
      <text class="state-label state-alpha" x="634" y="340">BRIDGE</text>
      <text class="state-label state-theta" x="634" y="396.5">THETA</text>
      <text class="state-label state-theta" x="634" y="417">CONSCIOUS MIND</text>
      <text class="state-label state-delta" x="634" y="470.5">DELTA</text>
      <text class="state-label state-delta" x="634" y="490.5">CONSCIOUS MIND</text>
    </g>
  </svg>
</main>
</body>
</html>
```